Harborline Renewal Business Card Design

Professional and clean design. The design colors should flow with the logo. Two-sided card with the website on the back which is:

www.HarborlineRenewal.example.

"Specializing in Water Damage Restoration"

On the front I need the name, email, phone, and logo.

Name: Darnell Quisby
Email: Darnell@HarborlineRenewal.example
Phone: 555-318-2046 for now

I only have the Preview and Thumbnail right now but should have the source files uploaded within a day or two.

Target Market(s)

Flood victims, home owners with water damage from busted pipes etc...

Industry/Entity Type

Business

Contact Information for Business Card

Name: Darnell Quisby

Font styles to use
Serif
Sans Serif

Requirements
Must have
• Business Card Details Info

```html
<!DOCTYPE html>
<html lang="en">
<head>
<meta charset="utf-8">
<title>Harborline Renewal – Business Card</title>
<link href="https://fonts.googleapis.com/css2?family=Cinzel:wght@400;600;700&family=Open+Sans:wght@400;600&display=swap" rel="stylesheet">
<style>
  :root {
    --ink: #050608;
    --sky: #5bc0ef;
    --ocean: #2f98d6;
    --deep: #1f7fc0;
    --paper: #ffffff;
    --stage: #d9dde1;
  }
  html, body {
    margin: 0;
    padding: 0;
    width: 1200px;
    height: 1120px;
    overflow: hidden;
    background: var(--stage);
  }
  .canvas {
    position: relative;
    width: 1200px;
    height: 1120px;
  }
  .card {
    position: absolute;
    left: 150px;
    width: 900px;
    height: 514px;
    background: var(--ink);
    overflow: hidden;
    box-shadow: 0 6px 18px rgba(0,0,0,0.25);
  }
  .card--back { top: 26px; }
  .card--front { top: 580px; }

  /* Back */
  .back-mark {
    position: absolute;
    left: 0; right: 0;
    top: 70px;
    display: flex;
    flex-direction: column;
    align-items: center;
    gap: 26px;
  }
  .back-mark .dot {
    width: 190px; height: 190px;
    border-radius: 50%;
    background: var(--sky);
  }
  .back-mark .brand {
    font-family: "Cinzel", serif;
    font-weight: 600;
    font-size: 34px;
    letter-spacing: 2px;
    color: var(--ocean);
  }
  .tagline {
    position: absolute;
    left: 0; right: 0;
    top: 420px;
    text-align: center;
    font-family: "Cinzel", serif;
    font-size: 25px;
    letter-spacing: 1px;
    color: var(--ocean);
  }

  /* Front */
  .wave { position: absolute; inset: 0; }
  .front-brand {
    position: absolute;
    left: 60px;
    top: 56px;
    display: flex;
    flex-direction: column;
    align-items: center;
    gap: 14px;
    width: 380px;
  }
  .front-brand .dot {
    width: 104px; height: 104px;
    border-radius: 50%;
    background: var(--sky);
  }
  .front-brand .brand {
    font-family: "Cinzel", serif;
    font-weight: 600;
    font-size: 36px;
    letter-spacing: 1px;
    color: var(--ocean);
    white-space: nowrap;
  }
  .person {
    position: absolute;
    right: 30px;
    top: 34px;
    text-align: right;
    font-family: "Cinzel", serif;
  }
  .person .name {
    font-size: 30px;
    font-weight: 600;
    color: var(--paper);
    letter-spacing: 1px;
  }
  .person .title {
    font-size: 24px;
    color: var(--ocean);
    letter-spacing: 1px;
  }
  .contact {
    position: absolute;
    right: 34px;
    top: 260px;
    text-align: right;
    font-family: "Open Sans", sans-serif;
    font-size: 19px;
    color: var(--paper);
    line-height: 32px;
  }
  .contact .row {
    display: flex;
    justify-content: flex-end;
    align-items: center;
    gap: 8px;
  }
  .contact svg { width: 17px; height: 17px; }
  .contact .address { margin-top: 14px; }
</style>
</head>
<body>
<div class="canvas">

  <section class="card card--back" aria-label="Card back">
    <div class="back-mark">
      <div class="dot"></div>
      <div class="brand">Harborline Renewal</div>
    </div>
    <div class="tagline">Specializing in Water Damage Restoration</div>
  </section>

  <section class="card card--front" aria-label="Card front">
    <svg class="wave" viewBox="0 0 900 514" preserveAspectRatio="none" aria-hidden="true">
      <path d="M0,392 C230,470 360,400 500,275 C630,160 760,130 900,118 L900,514 L0,514 Z" fill="var(--ocean)"/>
      <path d="M0,392 C230,470 360,400 500,275 C630,160 760,130 900,118" fill="none" stroke="var(--sky)" stroke-width="14"/>
      <path d="M0,408 C230,486 360,418 505,292 C632,180 760,150 900,140" fill="none" stroke="var(--ink)" stroke-width="9"/>
      <path d="M0,430 C240,500 380,436 520,320 C640,214 770,176 900,168" fill="none" stroke="var(--ink)" stroke-width="4"/>
      <path d="M0,446 C240,512 380,452 530,336" fill="none" stroke="var(--sky)" stroke-width="6"/>
    </svg>

    <div class="front-brand">
      <div class="dot"></div>
      <div class="brand">Harborline Renewal</div>
    </div>

    <div class="person">
      <div class="name">Darnell Quisby</div>
      <div class="title">Title</div>
    </div>

    <div class="contact">
      <div class="row">
        <svg viewBox="0 0 24 24" aria-hidden="true"><circle cx="12" cy="12" r="11" fill="none" stroke="#fff" stroke-width="2"/><path d="M8 6c-1 1-1 3 1 6s4 5 6 5l2-2-2-2-2 1c-1-1-2-2-3-4l1-2-2-2z" fill="#fff"/></svg>
        <span>555-318-2046</span>
      </div>
      <div class="row">
        <svg viewBox="0 0 24 24" aria-hidden="true"><rect x="2" y="5" width="20" height="14" rx="2" fill="#fff"/><path d="M2 6l10 7 10-7" fill="none" stroke="var(--ocean)" stroke-width="2"/></svg>
        <span>Darnell@HarborlineRenewal.example</span>
      </div>
      <div class="row">
        <svg viewBox="0 0 24 24" aria-hidden="true"><circle cx="12" cy="12" r="10" fill="none" stroke="#fff" stroke-width="2"/><ellipse cx="12" cy="12" rx="4" ry="10" fill="none" stroke="#fff" stroke-width="2"/><path d="M2 12h20" stroke="#fff" stroke-width="2"/></svg>
        <span>www.HarborlineRenewal.example</span>
      </div>
      <div class="row address"><span>Street Name, City Name, Zipcode-12345</span></div>
    </div>
  </section>

</div>
</body>
</html>
```